Locksmith Business Cards

My father-in-law is in need of new business cards for his locksmith business and I need to impress him. Kindly help me out!

You can see the previous business card attached. It is a family run business in North Wales.

No individual names on the cards.

Key Things to Feature:
- The words "Prompt", "Local", "Reliable" (as you can see under the logo on the website)
- 24h Emergency Service
- Covering All of North Wales, the Wirral and Chester
- The color blue
- A key or a lock would be interesting (similar to the ones that come up when you google locksmith business card)

Optional (only if design includes bullet points, like the example below):
https://imgvaultcdn.net/samples/208314/55172/55172_3904821_208314_image.jpg
- Residential / Commercial / Automotive
- Alarms & Cameras
- Key Cutting & Safes

https://www.brynhafod-locksmiths.co.uk/

Industry/Entity Type

Locksmith

Contact Information for Business Card

01632 960 418
07700 900 362
brynhafodlocksmiths@mailvane.com
Brynhafod Locksmiths, The Willow Barn, 7 Tannery Rd., Llandudno LL99 4QX
www.brynhafod-locksmiths.co.uk

Requirements
Must have
• - The words "Prompt", "Local", "Reliable" (as you can see under the logo on the website)
• - 24h Emergency Service
• - Covering All of North Wales, the Wirral and Chester
Nice to have
• - A key or a lock would be interesting (similar to the ones that come up when you google locksmith business card)

```html
<!DOCTYPE html>
<html lang="en">
<head>
<meta charset="utf-8">
<title>Brynhafod Locksmiths – Business Cards</title>
<link rel="stylesheet" href="https://fonts.googleapis.com/css2?family=Roboto:wght@400;500;700&display=swap">
<style>
  :root{
    --navy:#232a68;
    --accent:#4a5ea6;
    --pale:#8d9bd6;
    --white:#ffffff;
    --stage:#2b2d33;
    --card-w:640px;
    --card-h:380px;
  }
  *{box-sizing:border-box;margin:0;padding:0}
  html,body{width:1200px;height:900px;overflow:hidden}
  body{
    background:var(--stage);
    font-family:'Roboto',Arial,sans-serif;
    display:flex;flex-direction:column;align-items:center;justify-content:center;gap:44px;
  }
  .card{
    position:relative;width:var(--card-w);height:var(--card-h);
    border-radius:22px;overflow:hidden;background:var(--navy);color:var(--white);
  }
  .card-front .curve{position:absolute;inset:0}
  .contact{position:absolute;left:32px;top:70px;width:260px}
  .contact .company{font-size:20px;font-weight:500;letter-spacing:.5px;text-transform:uppercase}
  .contact .address{font-size:14px;line-height:20px;margin-top:12px}
  .contact .lines{list-style:none;margin-top:14px;font-size:14px;line-height:22px}
  .contact .lines li{display:flex;align-items:center;gap:9px;white-space:nowrap}
  .contact .lines svg{width:12px;height:12px;flex:none}
  .brand{position:absolute;left:372px;top:120px;color:var(--navy)}
  .brand-row{display:flex;align-items:center;gap:12px}
  .brand-mark{width:42px;height:42px;border-radius:8px;background:var(--navy);flex:none}
  .brand-name{font-weight:700;font-size:26px;line-height:29px;text-transform:uppercase;letter-spacing:.5px}
  .tagline{font-size:16px;margin-top:10px;margin-left:2px;color:var(--navy)}

  .card-back{padding:36px 0 0 60px}
  .card-back .brand-row .brand-mark{background:var(--white)}
  .card-back .brand-name{color:var(--pale)}
  .service{font-size:22px;margin-top:14px}
  .services{list-style:none;margin-top:12px;font-size:18px;line-height:26px}
  .services li{display:flex;align-items:center;gap:14px}
  .services li::before{content:"";width:8px;height:8px;border-radius:50%;background:var(--white)}
  .coverage{font-size:15px;margin-top:14px;color:var(--pale)}
</style>
</head>
<body>
  <section class="card card-front">
    <svg class="curve" viewBox="0 0 640 380" aria-hidden="true">
      <path d="M358 0 C270 110 290 290 430 380" fill="none" stroke="var(--accent)" stroke-width="7"/>
      <path d="M372 0 C282 112 300 288 442 380 L640 380 L640 0 Z" fill="var(--white)"/>
    </svg>
    <div class="contact">
      <p class="company">Brynhafod Locksmiths</p>
      <p class="address">The Willow Barn, 7 Tannery Rd.,<br>Llandudno LL99 4QX</p>
      <ul class="lines">
        <li><svg viewBox="0 0 12 12"><path d="M2 1l2 0 1 3-1.5 1a7 7 0 0 0 3.5 3.5L8 7l3 1v2c0 1-1 1-1 1C5 11 1 7 1 2c0 0 0-1 1-1z" fill="#fff"/></svg>01632 960 418</li>
        <li><svg viewBox="0 0 12 12"><rect x="3" y="0.5" width="6" height="11" rx="1" fill="none" stroke="#fff"/></svg>07700 900 362</li>
        <li><svg viewBox="0 0 12 12"><rect x="0.5" y="2.5" width="11" height="7" fill="none" stroke="#fff"/><path d="M1 3l5 4 5-4" fill="none" stroke="#fff"/></svg>brynhafodlocksmiths@mailvane.com</li>
        <li><svg viewBox="0 0 12 12"><circle cx="6" cy="6" r="5.2" fill="none" stroke="#fff"/><path d="M1 6h10M6 1c-3 3-3 7 0 10M6 1c3 3 3 7 0 10" fill="none" stroke="#fff" stroke-width=".8"/></svg>www.brynhafod-locksmiths.co.uk</li>
      </ul>
    </div>
    <div class="brand">
      <div class="brand-row">
        <span class="brand-mark"></span>
        <p class="brand-name">Brynhafod<br>Locksmiths</p>
      </div>
      <p class="tagline">Prompt. Local. Reliable</p>
    </div>
  </section>

  <section class="card card-back">
    <div class="brand-row">
      <span class="brand-mark"></span>
      <p class="brand-name">Brynhafod<br>Locksmiths</p>
    </div>
    <p class="service">24h Emergency Service</p>
    <ul class="services">
      <li>Residential</li>
      <li>Commercial</li>
      <li>Automotive</li>
      <li>Alarms &amp; Cameras</li>
      <li>Key Cutting &amp; Safes</li>
    </ul>
    <p class="coverage">Covering All of North Wales, the Wirral and Chester</p>
  </section>
</body>
</html>
```